Request for Business Card Design

Hi. My name is Marlene, I am looking for a new business card design for my company, Quarrow Signal Instruments, LLC. I really like the design you did for Tarsel Venture and was hoping you could do something similar using our full logo and our mark. I am also open to any raised texture design using our mark. I have attached our full logo, which would need to be somewhere on the card, as well as the mark in both outline and full form, as well as our brand colors / guide. The card does not have to be white, as long as our logo and mark appear. I actually like darker colored business cards more, but am open to all options. If you are interested in working with me, please let me know. We would also take the business card design into letterhead design if you can do that.

```html
<!DOCTYPE html>
<html lang="en">
<head>
<meta charset="utf-8">
<title>Quarrow Signal Instruments – Business Card</title>
<link rel="stylesheet" href="https://fonts.googleapis.com/css2?family=Open+Sans:wght@400;600;800&display=swap">
<style>
  :root {
    --stage: #1f1f22;
    --card-dark: #3a3a3d;
    --brand-blue: #1497c4;
    --brand-blue-deep: #0d7fa8;
    --brand-blue-light: #48b8dd;
    --paper-white: #f4f4f4;
    --text-light: #f2f2f2;
  }
  * { box-sizing: border-box; margin: 0; padding: 0; }
  html, body {
    width: 1200px; height: 780px; overflow: hidden;
    background: var(--stage);
    font-family: "Open Sans", Arial, sans-serif;
  }
  .stage {
    width: 1200px; height: 780px;
    display: flex; align-items: center; justify-content: center; gap: 40px;
  }
  .card {
    position: relative; width: 540px; height: 310px; overflow: hidden;
    box-shadow: 0 10px 30px rgba(0,0,0,.45);
  }

  /* Front */
  .card-front { background: var(--card-dark); color: var(--text-light); }
  .front-swoosh { position: absolute; left: 0; bottom: 0; width: 540px; height: 310px; }
  .brand-lockup {
    position: absolute; left: 28px; top: 28px;
    display: flex; align-items: center; gap: 12px;
  }
  .brand-dot { width: 34px; height: 34px; border-radius: 50%; background: var(--brand-blue); }
  .brand-name {
    font-weight: 800; font-size: 19px; letter-spacing: .5px; color: var(--text-light);
  }
  .address {
    position: absolute; left: 28px; top: 118px;
    font-size: 12.5px; line-height: 1.45;
  }
  .person { position: absolute; right: 36px; top: 104px; text-align: right; }
  .person-name { font-weight: 800; font-size: 34px; line-height: 1; color: var(--brand-blue); }
  .person-role { font-size: 15px; margin-top: 4px; }
  .accent-bar {
    position: absolute; right: 0; top: 104px; width: 14px; height: 58px;
    background: var(--brand-blue);
  }
  .contact-list {
    position: absolute; right: 24px; bottom: 28px; list-style: none;
    font-size: 12.5px; line-height: 1.5;
  }
  .contact-item { display: flex; align-items: center; justify-content: flex-end; gap: 8px; }
  .contact-icon { width: 13px; height: 13px; flex: none; }

  /* Back */
  .card-back { background: var(--brand-blue); }
  .back-pattern {
    position: absolute; inset: 0;
    background: linear-gradient(100deg, var(--brand-blue-deep) 0%, var(--brand-blue) 55%, var(--brand-blue-light) 100%);
  }
  .back-lockup {
    position: absolute; right: 26px; bottom: 22px;
    display: flex; align-items: center; gap: 8px;
  }
  .back-lockup .brand-dot { width: 18px; height: 18px; background: var(--paper-white); }
  .back-lockup .brand-name { font-size: 12px; }
</style>
</head>
<body>
<main class="stage">

  <section class="card card-front" aria-label="Business card front">
    <svg class="front-swoosh" viewBox="0 0 540 310" aria-hidden="true">
      <path d="M0 150 C 120 170, 200 220, 265 310 L0 310 Z" fill="var(--brand-blue)"/>
      <path d="M0 176 C 105 192, 180 238, 232 310 L0 310 Z" fill="var(--card-dark)"/>
      <path d="M0 186 C 100 200, 170 244, 218 310 L0 310 Z" fill="var(--paper-white)"/>
    </svg>

    <div class="brand-lockup">
      <span class="brand-dot"></span>
      <span class="brand-name">Quarrow Signal Instruments</span>
    </div>

    <p class="address">1180 Ridgeway Park Drive<br>Fenmore, CO 80412</p>

    <div class="person">
      <h1 class="person-name">Marlene</h1>
      <p class="person-role">Director</p>
    </div>
    <span class="accent-bar"></span>

    <ul class="contact-list">
      <li class="contact-item">+001 555 210 4418
        <svg class="contact-icon" viewBox="0 0 16 16"><path d="M3 1h3l1.5 4-2 1.3a9 9 0 0 0 4.2 4.2L11 8.5l4 1.5v3a2 2 0 0 1-2 2A12 12 0 0 1 1 3a2 2 0 0 1 2-2z" fill="var(--brand-blue)"/></svg>
      </li>
      <li class="contact-item">+001 555 210 4419
        <svg class="contact-icon" viewBox="0 0 16 16"><rect x="4" y="1" width="8" height="5" fill="none" stroke="var(--brand-blue)" stroke-width="1.5"/><rect x="1" y="6" width="14" height="7" rx="1" fill="var(--brand-blue)"/><rect x="4" y="10" width="8" height="5" fill="var(--card-dark)" stroke="var(--brand-blue)" stroke-width="1.2"/></svg>
      </li>
      <li class="contact-item">www.quarrowsignal.com
        <svg class="contact-icon" viewBox="0 0 16 16"><circle cx="8" cy="8" r="6.5" fill="none" stroke="var(--brand-blue)" stroke-width="1.5"/><ellipse cx="8" cy="8" rx="2.8" ry="6.5" fill="none" stroke="var(--brand-blue)" stroke-width="1.2"/><path d="M1.5 8h13" stroke="var(--brand-blue)" stroke-width="1.2"/></svg>
      </li>
      <li class="contact-item">info@quarrowsignal.com
        <svg class="contact-icon" viewBox="0 0 16 16"><rect x="1" y="3" width="14" height="10" rx="1" fill="var(--brand-blue)"/><path d="M1.5 3.5 8 9l6.5-5.5" fill="none" stroke="var(--card-dark)" stroke-width="1.3"/></svg>
      </li>
    </ul>
  </section>

  <section class="card card-back" aria-label="Business card back">
    <div class="back-pattern" role="img" aria-label="Repeating brand mark texture in blue tones"></div>
    <div class="back-lockup">
      <span class="brand-dot"></span>
      <span class="brand-name">Quarrow Signal Instruments</span>
    </div>
  </section>

</main>
</body>
</html>
```